Northfield Builders Guild Business card

We are looking for a new business card design with photo included.
Our business is a nonprofit construction contractor membership organization. We offer business education, assist with business setup and licensing, provide safety training, and provide a member directory.
URL: www.builderslinkguild.org
Color code:
CMYK: 0 cyan, 42 magenta, 100 yellow, 0 black for Print.
Hexidecimal: #FF9900
RGB: R 255; G 153; B 0

```html
<!DOCTYPE html>
<html lang="en">
<head>
<meta charset="utf-8">
<title>Northfield Builders Guild – Business Card</title>
<link href="https://fonts.googleapis.com/css2?family=Arimo:wght@400;700&display=swap" rel="stylesheet">
<style>
  :root {
    --brand-orange: #FF9900;
    --ink-dark: #1c1c1c;
    --ink-grey: #666666;
    --rule-grey: #8a8a8a;
    --card-white: #ffffff;
    --card-charcoal: #2f2f2f;
    --emboss-grey: #5a5a5a;
    --backdrop: #ececec;
    --photo-light: #e9e9ea;
    --photo-mid: #b9c0cc;
    --photo-dark: #33415c;
  }
  * { box-sizing: border-box; margin: 0; padding: 0; }
  html, body {
    width: 1200px; height: 801px; overflow: hidden;
    background: var(--backdrop);
    font-family: "Arimo", Arial, sans-serif;
  }
  .sheet {
    position: relative; width: 1200px; height: 801px;
    display: flex; align-items: center; justify-content: center; gap: 40px;
  }
  .card {
    position: relative; width: 540px; height: 309px;
    border-bottom: 5px solid var(--brand-orange);
    box-shadow: 0 10px 24px rgba(0,0,0,0.18);
    overflow: hidden;
  }
  .card--front { background: var(--card-white); }
  .card--back { background: var(--card-charcoal); }

  .brand-name {
    position: absolute; left: 30px; top: 36px;
    font-weight: 700; font-size: 23px; letter-spacing: 0.5px;
    color: var(--ink-dark); text-transform: uppercase; line-height: 1;
    white-space: nowrap;
  }
  .portrait {
    position: absolute; left: 62px; top: 98px;
    width: 176px; height: 176px; border-radius: 50%;
    border: 3px solid #bdbdbd;
    background: radial-gradient(circle at 50% 40%, var(--photo-light) 0%, var(--photo-mid) 70%, var(--photo-dark) 100%);
  }
  .divider {
    position: absolute; left: 282px; top: 92px;
    width: 1px; height: 180px; background: var(--rule-grey);
  }
  .details {
    position: absolute; left: 302px; top: 90px; right: 16px;
    color: var(--ink-grey); font-size: 13px; line-height: 1.35;
  }
  .details .person { color: var(--brand-orange); font-weight: 700; font-size: 21px; line-height: 1.1; }
  .details .role { font-size: 14px; margin-bottom: 12px; }
  .details .address { margin-bottom: 12px; }
  .contact { display: flex; align-items: center; gap: 8px; margin-bottom: 3px; white-space: nowrap; }
  .contact svg { width: 14px; height: 14px; flex: none; }
  .web-accent { color: var(--brand-orange); }

  .back-mark {
    position: absolute; inset: 0;
    display: flex; align-items: center; justify-content: center;
    text-align: center;
    font-weight: 700; font-size: 40px; line-height: 1.05;
    text-transform: uppercase; color: var(--emboss-grey);
  }
</style>
</head>
<body>
<main class="sheet">
  <section class="card card--front" aria-label="Business card front">
    <div class="brand-name">Northfield Builders Guild</div>
    <div class="portrait" role="img" aria-label="Portrait photo of the card holder in a suit"></div>
    <div class="divider"></div>
    <div class="details">
      <div class="person">Daniel Harper</div>
      <div class="role">Manager</div>
      <div class="address">Your address, city<br>state, ZIP 0000</div>
      <div class="contact">
        <svg viewBox="0 0 16 16" aria-hidden="true"><path fill="#FF9900" d="M3.5 1.5l2.5 0 1 3.5-1.6 1.2c.8 1.7 2.1 3 3.8 3.8L10.4 8.4l3.5 1v2.6c0 .8-.7 1.5-1.5 1.5C6.7 13.5 2 8.8 2 3c0-.8.7-1.5 1.5-1.5z"/></svg>
        <span>555-318-4470</span>
      </div>
      <div class="contact">
        <svg viewBox="0 0 16 16" aria-hidden="true"><rect x="1" y="3" width="14" height="10" fill="#FF9900"/><path d="M1.5 3.5L8 9l6.5-5.5" fill="none" stroke="#fff" stroke-width="1.2"/></svg>
        <span>contact@builderslinkguild.org</span>
      </div>
      <div class="contact">
        <svg viewBox="0 0 16 16" aria-hidden="true"><circle cx="8" cy="8" r="6.5" fill="#FF9900"/><circle cx="8" cy="8" r="2.5" fill="#fff"/></svg>
        <span>www.<span class="web-accent">builderslinkguild</span>.org</span>
      </div>
    </div>
  </section>

  <section class="card card--back" aria-label="Business card back">
    <div class="back-mark">Northfield<br>Builders Guild</div>
  </section>
</main>
</body>
</html>
```